Commercial Real Estate

We need a business card design for a new commercial real estate business that specializes in apartment building brokerage. Not individual units but the entire complex. We find and represent the owners existing buildings and well as new buyers for those buildings. The design should convey trust, integrity, knowledge and growth. It should be easily read.

Target Market(s)

40 to 65 years old

Industry/Entity Type

Real Estate

```html
<!DOCTYPE html>
<html lang="en">
<head>
<meta charset="utf-8">
<title>Keystone Row – Business Card</title>
<link href="https://fonts.googleapis.com/css2?family=Noto+Sans:wght@400;700&display=swap" rel="stylesheet">
<style>
  :root {
    --teal: #4fb3b0;
    --slate: #3e5b5a;
    --ink: #4a4d4f;
    --paper: #ffffff;
    --backdrop: #e8e9ea;
  }
  html, body {
    margin: 0;
    width: 1200px;
    height: 720px;
    overflow: hidden;
    background: var(--backdrop);
    font-family: "Noto Sans", Verdana, sans-serif;
  }
  .stage {
    position: relative;
    width: 1200px;
    height: 720px;
  }
  .card {
    position: absolute;
    top: 206px;
    width: 540px;
    height: 309px;
    background: var(--paper);
    box-shadow: 0 2px 6px rgba(0,0,0,0.08);
    overflow: hidden;
  }
  .card--front { left: 40px; }
  .card--back { left: 620px; }

  .brand {
    position: absolute;
    top: 44px;
    right: 36px;
    display: flex;
    align-items: center;
    gap: 10px;
  }
  .brand__dot {
    width: 14px;
    height: 14px;
    background: var(--teal);
  }
  .brand__name {
    font-size: 24px;
    font-weight: 400;
    letter-spacing: 2px;
    color: var(--slate);
    text-transform: uppercase;
  }

  .address {
    position: absolute;
    top: 104px;
    right: 36px;
    margin: 0;
    text-align: right;
    font-size: 17px;
    line-height: 1.35;
    color: var(--ink);
    font-style: normal;
  }

  .accent {
    position: absolute;
    left: 0;
    width: 8px;
  }
  .accent--name { top: 180px; height: 46px; background: var(--teal); }
  .accent--contact { top: 236px; height: 73px; background: var(--slate); }

  .person {
    position: absolute;
    left: 26px;
    top: 174px;
  }
  .person__name {
    margin: 0;
    font-size: 21px;
    font-weight: 700;
    letter-spacing: 1px;
    color: var(--teal);
    text-transform: uppercase;
    line-height: 1.2;
  }
  .person__title {
    margin: 0;
    font-size: 16px;
    color: var(--ink);
    line-height: 1.3;
  }

  .contacts {
    position: absolute;
    left: 26px;
    top: 236px;
    margin: 0;
    padding: 0;
    list-style: none;
  }
  .contacts__item {
    display: flex;
    align-items: center;
    gap: 10px;
    font-size: 16px;
    line-height: 23px;
    color: var(--ink);
  }
  .contacts__icon {
    width: 16px;
    height: 16px;
    flex: none;
  }
  .contacts__domain { color: var(--teal); }
</style>
</head>
<body>
<main class="stage">
  <section class="card card--front" aria-label="Business card, front">
    <div class="brand">
      <span class="brand__dot"></span>
      <span class="brand__name">Keystone Row</span>
    </div>

    <address class="address">PO. BOX 2400<br>Harbor Lane, Fairview City</address>

    <span class="accent accent--name"></span>
    <span class="accent accent--contact"></span>

    <div class="person">
      <p class="person__name">Daniel Hartley</p>
      <p class="person__title">Managing Director</p>
    </div>

    <ul class="contacts">
      <li class="contacts__item">
        <svg class="contacts__icon" viewBox="0 0 16 16" aria-hidden="true">
          <path d="M2 5c0-2 2-3 6-3s6 1 6 3v1h-3V4.5H5V6H2z" fill="var(--teal)"/>
          <rect x="3" y="7" width="10" height="7" rx="1" fill="var(--teal)"/>
          <circle cx="8" cy="10.5" r="1.8" fill="#fff"/>
        </svg>
        <span>00 00 00 00 00</span>
      </li>
      <li class="contacts__item">
        <svg class="contacts__icon" viewBox="0 0 16 16" aria-hidden="true">
          <rect x="1" y="3" width="14" height="10" fill="var(--teal)"/>
          <path d="M1.5 3.5 8 9l6.5-5.5" fill="none" stroke="#fff" stroke-width="1.2"/>
        </svg>
        <span>daniel@keystonerow.com</span>
      </li>
      <li class="contacts__item">
        <svg class="contacts__icon" viewBox="0 0 16 16" aria-hidden="true">
          <circle cx="8" cy="8" r="7" fill="var(--teal)"/>
          <g fill="none" stroke="#fff" stroke-width="0.9">
            <ellipse cx="8" cy="8" rx="3" ry="7"/>
            <path d="M1 8h14M2.5 4.5h11M2.5 11.5h11M8 1v14"/>
          </g>
        </svg>
        <span>www.<span class="contacts__domain">keystonerow</span>.com</span>
      </li>
    </ul>
  </section>

  <section class="card card--back" aria-label="Business card, back"></section>
</main>
</body>
</html>
```